Business Card for Coastal Tundrabridge Advisory

We need a business card for Coastal Tundrabridge Advisory. The company website address is provided below. The company logo is attached. We provide specialized permafrost services to the mining, transportation, and oil & gas industries. The card should be prepared for:
Matthias Korhonen, PhD.
Coastal Tundrabridge Advisory
PO Box 418259
Quillwater, Alaska 99642
Direct: +1-907-555-0143
Email: mkorhonen@tundrabridgeadvisory.example
Website: www.coastaltundrabridgeadvisory.example

```html
<!DOCTYPE html>
<html lang="en">
<head>
<meta charset="utf-8">
<title>Coastal Tundrabridge Advisory – Business Card</title>
<link href="https://fonts.googleapis.com/css2?family=Arimo:wght@400;700&display=swap" rel="stylesheet">
<style>
  :root {
    --backdrop: #9d9d9d;
    --card-light: #f7f7f5;
    --card-dark: #0f161d;
    --ink: #1f252c;
    --ink-soft: #8a8d91;
    --rule: #b9bbbd;
    --paper-white: #ffffff;
  }
  * { box-sizing: border-box; margin: 0; padding: 0; }
  html, body { width: 1200px; height: 1050px; overflow: hidden; }
  body {
    background: var(--backdrop);
    font-family: "Arimo", Arial, sans-serif;
    color: var(--ink);
    position: relative;
  }
  .card {
    position: absolute;
    left: 180px;
    width: 840px;
    height: 480px;
    border-radius: 26px;
    box-shadow: 0 6px 18px rgba(0,0,0,0.18);
  }
  .card--front { top: 30px; background: var(--card-light); }
  .card--back  { top: 540px; background: var(--card-dark); }

  .wordmark {
    position: absolute;
    font-weight: 700;
    font-size: 38px;
    letter-spacing: 0.5px;
    white-space: nowrap;
  }
  .card--front .wordmark { left: 110px; top: 100px; color: var(--ink); }
  .card--back .wordmark  { left: 0; right: 0; top: 212px; text-align: center; color: var(--paper-white); }

  .identity {
    position: absolute;
    right: 370px;
    top: 205px;
    text-align: right;
  }
  .identity__name { font-weight: 700; font-size: 27px; }
  .identity__role { font-size: 19px; color: var(--ink-soft); margin-top: 6px; }
  .identity__links { margin-top: 18px; font-size: 16px; line-height: 27px; }
  .link-row { display: flex; align-items: center; justify-content: flex-end; gap: 8px; }
  .link-row svg { width: 16px; height: 16px; flex: none; }

  .divider {
    position: absolute;
    left: 490px;
    top: 268px;
    width: 1px;
    height: 110px;
    background: var(--rule);
  }

  .contact {
    position: absolute;
    left: 512px;
    top: 272px;
    font-size: 19px;
    line-height: 30px;
  }
  .contact__phone { display: flex; align-items: center; gap: 10px; margin-bottom: 6px; }
  .contact__phone svg { width: 16px; height: 16px; }
</style>
</head>
<body>

<section class="card card--front" aria-label="Business card front">
  <div class="wordmark">Coastal Tundrabridge Advisory</div>

  <div class="identity">
    <div class="identity__name">Matthias Korhonen, PhD.</div>
    <div class="identity__role">President</div>
    <div class="identity__links">
      <div class="link-row">
        <span>mkorhonen@tundrabridgeadvisory.example</span>
        <svg viewBox="0 0 16 16" aria-hidden="true"><rect x="1" y="3" width="14" height="10" rx="1.5" fill="var(--ink)"/><path d="M2 4.5 L8 9 L14 4.5" stroke="var(--card-light)" stroke-width="1.3" fill="none"/></svg>
      </div>
      <div class="link-row">
        <span>www.coastaltundrabridgeadvisory.example</span>
        <svg viewBox="0 0 16 16" aria-hidden="true"><circle cx="8" cy="8" r="7" fill="var(--ink)"/><ellipse cx="8" cy="8" rx="3" ry="7" stroke="var(--card-light)" stroke-width="1" fill="none"/><path d="M1 8 H15" stroke="var(--card-light)" stroke-width="1"/></svg>
      </div>
    </div>
  </div>

  <div class="divider"></div>

  <div class="contact">
    <div class="contact__phone">
      <svg viewBox="0 0 16 16" aria-hidden="true"><path d="M4 1.5 L6.2 4.6 L4.8 6.3 C5.6 8 7.9 10.4 9.7 11.2 L11.4 9.8 L14.5 12 L13 14.5 C7.5 14.5 1.5 8.5 1.5 3 Z" fill="var(--ink)"/></svg>
      <span>+1-907-555-0143</span>
    </div>
    <div>PO Box 418259</div>
    <div>Quillwater, Alaska 99642</div>
  </div>
</section>

<section class="card card--back" aria-label="Business card back">
  <div class="wordmark">Coastal Tundrabridge Advisory</div>
</section>

</body>
</html>
```